Develop website for Cloud Security Startup

Looking for a logo that conveys the outsourced security and management of clients data, systems and development in Tellix, Bri and Pindle with an emphasis on security and compliance

Target Market(s)

Companies looking for professional services IT firm

Coding

Coded - Design and coding required

Number of Pages Required

5+ page

Font styles to use
Sans Serif

Colors
0455a3
33a6d7

Requirements
Must have
• Landing Page
- Help me get started

Move to the cloud safely
- Benefits of Cloud

What we do
- Cloud Adoption
- Managed Services
- Optimise

Resources
- News
- Resources
- Events
- Webinars
- Not for profit
- Case Studies
- Support Button
- Incident Button

Company
- About Us
- Why Vorplexa?
- Acreditations
- Quorvane Tellix Partner
- Net Promoter Score
- Careers
- Contact Us

Contact Us

```html
<!DOCTYPE html>
<html lang="en">
<head>
<meta charset="utf-8">
<title>Vorplexa — Effective Technology Management</title>
<link rel="stylesheet" href="https://fonts.googleapis.com/css2?family=Exo+2:wght@600;700;800&family=Montserrat:wght@400;500;600;700&display=swap">
<style>
:root{
  --navy:#06357f;
  --deep:#0455a3;
  --sky:#33a6d7;
  --cyan:#1ba3e0;
  --ink:#111827;
  --text:#2c2c2c;
  --muted:#6b7280;
  --line:#d6dbe3;
  --white:#ffffff;
  --night:#03060d;
}
*{box-sizing:border-box;margin:0;padding:0}
html,body{width:1200px;height:4515px;overflow:hidden;background:var(--white)}
body{position:relative;font-family:"Montserrat",sans-serif;color:var(--text)}
.abs{position:absolute}
.heading{font-family:"Exo 2",sans-serif;font-weight:800;font-size:30px;letter-spacing:.5px;color:var(--ink);text-transform:uppercase}
.heading .accent{color:var(--sky)}
.rule{position:absolute;height:3px;width:82px;background:var(--sky)}
.btn{position:absolute;display:flex;align-items:center;justify-content:center;font-size:12px;font-weight:700;letter-spacing:.3px;text-transform:uppercase;color:var(--white);background:var(--navy);border-radius:3px}

/* header */
.site-header{left:0;top:0;width:1200px;height:105px;background:var(--white)}
.brand{display:flex;align-items:center;gap:10px}
.brand-dot{width:34px;height:34px;border-radius:50%;background:var(--deep)}
.brand-name{font-family:"Montserrat",sans-serif;font-weight:700;color:var(--deep);font-size:22px;letter-spacing:1px}
.nav{left:470px;top:40px;display:flex;gap:0;font-size:14px;font-weight:500;color:#1d2a44}
.nav a{position:absolute;white-space:nowrap;text-decoration:none;color:inherit}
.nav a.active{color:var(--sky)}

/* hero */
.hero-title{left:110px;top:282px;font-family:"Exo 2",sans-serif;font-weight:800;font-size:58px;color:var(--white);letter-spacing:2px}
.hero-sub{left:110px;top:356px;width:430px;font-size:17px;line-height:25px;font-weight:500;color:var(--white)}
.dots{left:114px;top:502px;display:flex;gap:8px}
.dots span{width:10px;height:10px;border-radius:50%;border:1.5px solid #cfd8e6}
.dots span.on{background:var(--sky);border-color:var(--sky)}

/* about */
.about-text{left:599px;top:878px;width:490px;font-size:13.6px;line-height:24.7px;color:var(--text)}

/* services */
.service{position:absolute;top:1465px;width:308px;height:306px;border-radius:4px;overflow:hidden;box-shadow:0 8px 18px rgba(0,40,90,.35)}
.service .photo{position:absolute;inset:0}
.service .label{position:absolute;left:0;right:0;bottom:0;height:90px;display:flex;align-items:flex-end;justify-content:center;padding-bottom:24px;background:linear-gradient(rgba(0,0,0,0),rgba(0,0,0,.75));font-size:19px;font-weight:600;color:var(--white)}

/* benefits */
.benefit-label{position:absolute;font-size:15.5px;font-weight:500;color:#1d1d1d;white-space:nowrap}
.benefit-icon{position:absolute;width:56px;height:56px;border-radius:50%;background:var(--sky);border:3px solid #fff;box-shadow:0 0 0 1px #9fd6ee}

/* news */
.news-card{position:absolute;background:var(--white);border-radius:4px;overflow:hidden}
.news-date{font-size:13.5px;font-weight:700;color:var(--deep)}
.news-title{font-weight:700;color:var(--ink)}
.news-body{color:#4a4a4a}
.read-more{color:var(--sky);font-weight:500}

/* contact */
.field{position:absolute;border:1px solid var(--line);border-radius:2px;background:#fff;display:flex;align-items:center;gap:14px;padding-left:12px;font-size:12px;color:#8a8f98;text-transform:uppercase}
.field svg{flex:none}

/* footer */
.foot-head{position:absolute;font-size:16px;font-weight:700;color:var(--sky);text-transform:uppercase;letter-spacing:.3px}
.foot-list{position:absolute;list-style:none;font-size:13px;color:#e6ecf5;text-transform:uppercase}
.foot-list li{height:28.3px;display:flex;align-items:center;gap:10px}
.foot-list li::before{content:"";width:5px;height:5px;border-radius:50%;background:var(--sky)}
.social{position:absolute;width:48px;height:48px;border-radius:50%;background:#fff}
.bottom-bar{left:0;top:4432px;width:1200px;height:83px;background:var(--navy);color:#fff;font-size:13.5px;font-weight:500}
</style>
</head>
<body>

<!-- header -->
<header class="site-header abs">
  <div class="brand abs" style="left:110px;top:34px">
    <span class="brand-dot"></span><span class="brand-name">VORPLEXA</span>
  </div>
  <nav class="nav abs">
    <a class="active" style="left:2px">HOME</a>
    <a style="left:87px">WHAT WE DO</a>
    <a style="left:226px">RESOURCES</a>
    <a style="left:357px">COMPANY</a>
    <a style="left:473px">CONTACT</a>
  </nav>
  <div class="abs" style="left:1046px;top:38px;width:2px;height:26px;background:var(--sky)"></div>
  <svg class="abs" style="left:1068px;top:42px" width="20" height="20" viewBox="0 0 20 20"><circle cx="8" cy="8" r="6" fill="none" stroke="#33a6d7" stroke-width="2.2"/><line x1="12.5" y1="12.5" x2="18" y2="18" stroke="#33a6d7" stroke-width="2.4" stroke-linecap="round"/></svg>
</header>

<!-- hero -->
<section class="hero">
  <div class="abs" role="img" aria-label="Engineer working at a bank of monitors in a dim blue operations room" style="left:0;top:105px;width:1200px;height:615px;background:radial-gradient(circle at 78% 35%,#3d6fa3 0%,#1a3c66 35%,#0b1f3c 70%,#07142a 100%)"></div>
  <svg class="abs" style="left:0;top:640px" width="1200" height="90" viewBox="0 0 1200 90">
    <polygon points="0,22 860,60 1200,22 1200,90 0,90" fill="#ffffff"/>
    <polygon points="330,32 860,60 1200,22 1200,30 860,78" fill="#1ba3e0"/>
    <polygon points="860,60 1200,22 1200,30 860,78" fill="#0e8fd0"/>
  </svg>
  <div class="hero-title abs">VORPLEXA</div>
  <p class="hero-sub abs">Perspiciatis unde omnis istenatus error sitvolu ptatem accusantium doloremque.</p>
  <div class="btn" style="left:110px;top:433px;width:220px;height:37px">Help me get started</div>
  <div class="dots abs"><span class="on"></span><span></span><span></span><span></span><span></span></div>
  <svg class="abs" style="left:28px;top:360px" width="56" height="56" viewBox="0 0 56 56"><circle cx="28" cy="28" r="26" fill="none" stroke="#fff" stroke-width="2"/><path d="M38 28H19M26 21l-7 7 7 7" fill="none" stroke="#fff" stroke-width="2.2" stroke-linecap="round" stroke-linejoin="round"/></svg>
  <svg class="abs" style="left:1114px;top:360px" width="56" height="56" viewBox="0 0 56 56"><circle cx="28" cy="28" r="26" fill="none" stroke="#fff" stroke-width="2"/><path d="M18 28h19M30 21l7 7-7 7" fill="none" stroke="#fff" stroke-width="2.2" stroke-linecap="round" stroke-linejoin="round"/></svg>
</section>

<!-- about -->
<section class="about">
  <div class="abs" style="left:150px;top:780px;width:340px;height:340px;border-radius:50%;background:linear-gradient(135deg,#0a3d91,#1ba3e0);display:flex;align-items:center;justify-content:center">
    <span style="font-weight:700;font-size:40px;color:#fff;letter-spacing:2px">VORPLEXA</span>
  </div>
  <h2 class="heading abs" style="left:599px;top:806px">About <span class="accent">us</span></h2>
  <div class="rule" style="left:599px;top:857px"></div>
  <p class="about-text abs">Perspiciatis unde omnis iste natus error sit voluptatem accusantium doloremque laudantium, totam rem aperiam, eaque ipsa quae ab illo inventore veritatis et quasi architecto beatae vitae dicta sunt explicabo. Nemo enim ipsam voluptatem quia voluptas sit aspernatur aut odit aut fugit, sed quia consequuntur magni dolores eos qui ratione voluptatem sequi nesciunt. Neque porro quisquam est, qui dolorem ipsum quia dolor sit amet.</p>
  <div class="btn" style="left:599px;top:1076px;width:151px;height:42px">Learn more</div>
</section>

<!-- what we do -->
<section class="services">
  <svg class="abs" style="left:0;top:1205px" width="1200" height="80" viewBox="0 0 1200 80">
    <polygon points="0,80 0,60 105,55 342,10 1200,70 1200,80" fill="#0a3d91"/>
    <polygon points="0,80 0,70 105,60 342,22 1200,72 1200,80" fill="#1ba3e0"/>
  </svg>
  <div class="abs" role="img" aria-label="Faint control room backdrop in bright blue" style="left:0;top:1275px;width:1200px;height:582px;background:linear-gradient(180deg,#1c9fdc 0%,#22a9e3 50%,#1da2df 100%)"></div>
  <h2 class="heading abs" style="left:0;width:1200px;text-align:center;top:1347px;color:#fff">What we do</h2>
  <div class="service" style="left:110px">
    <div class="photo" role="img" aria-label="Team gathered around a laptop in an office" style="background:linear-gradient(160deg,#c9d3dd,#6d7f92 55%,#2c3b4c)"></div>
    <div class="label">CLOUD ADOPTION</div>
  </div>
  <div class="service" style="left:445px">
    <div class="photo" role="img" aria-label="Engineer at a workstation with monitors" style="background:linear-gradient(160deg,#4d7fb2,#1f3e64 55%,#0f1d33)"></div>
    <div class="label">MANAGED SERVICES</div>
  </div>
  <div class="service" style="left:780px">
    <div class="photo" role="img" aria-label="City skyline at dusk with glowing network arcs" style="background:linear-gradient(180deg,#e0894a 0%,#7a5a5e 35%,#1c3550 65%,#0b1e33 100%)"></div>
    <div class="label">OPTIMISE</div>
  </div>
</section>

<!-- benefits -->
<section class="benefits">
  <h2 class="heading abs" style="left:0;width:1200px;text-align:center;top:1937px">Benefits <span class="accent">of cloud</span></h2>
  <div class="rule" style="left:559px;top:1988px"></div>
  <svg class="abs" style="left:447px;top:2020px" width="280" height="280" viewBox="0 0 280 280"><circle cx="140" cy="140" r="135" fill="none" stroke="#0a3d91" stroke-width="1.6" stroke-dasharray="6 5"/></svg>
  <div class="abs" style="left:527px;top:2100px;width:120px;height:120px;border-radius:50%;background:linear-gradient(135deg,#0a3d91,#1ba3e0);display:flex;align-items:center;justify-content:center">
    <span style="font-weight:700;font-size:17px;color:#fff;letter-spacing:1px">VORPLEXA</span>
  </div>
  <div class="benefit-icon" style="left:480px;top:2032px"></div>
  <div class="benefit-icon" style="left:646px;top:2032px"></div>
  <div class="benefit-icon" style="left:442px;top:2183px"></div>
  <div class="benefit-icon" style="left:689px;top:2188px"></div>
  <div class="benefit-icon" style="left:559px;top:2272px"></div>
  <div class="benefit-label" style="right:741px;top:2045px">PERSPICIATIS UNDOMNIS</div>
  <div class="benefit-label" style="left:715px;top:2045px">PERSPICIATIS UNDOMNIS</div>
  <div class="benefit-label" style="right:774px;top:2208px">PERSPICIATIS UNDOMNIS</div>
  <div class="benefit-label" style="left:766px;top:2208px">PERSPICIATIS UNDOMNIS</div>
  <div class="benefit-label" style="left:0;width:1200px;text-align:center;top:2339px">PERSPICIATIS UNDOMNIS</div>
</section>

<!-- news -->
<section class="news">
  <div class="abs" role="img" aria-label="Deep blue digital particle backdrop" style="left:0;top:2444px;width:1200px;height:902px;background:radial-gradient(circle at 80% 70%,#1a5ab8 0%,#0a3d91 40%,#062d73 100%)"></div>
  <svg class="abs" style="left:0;top:3280px" width="1200" height="70" viewBox="0 0 1200 70">
    <polygon points="0,0 0,22 860,62 1200,20 1200,70 0,70" fill="#ffffff"/>
    <polygon points="250,34 860,62 1200,20 1200,30 860,66" fill="#1ba3e0"/>
  </svg>
  <h2 class="heading abs" style="left:0;width:1200px;text-align:center;top:2524px;color:#fff">News</h2>

  <article class="news-card" style="left:109px;top:2598px;width:460px;height:564px">
    <div role="img" aria-label="Glowing cloud over a circuit pattern" style="height:293px;background:radial-gradient(circle at 55% 55%,#3aa0e8 0%,#1565b8 45%,#0b3a7a 100%)"></div>
    <div style="padding:24px 30px 0 30px">
      <div class="news-date">DEC 04, 2020</div>
      <div class="news-title" style="font-size:16px;line-height:28px;margin-top:20px">Sedut perspiciatis unde omnis iste natus error sit voluptatem accusantium</div>
      <div class="news-body" style="font-size:13px;line-height:29px;margin-top:6px">"Sed ut perspiciatis unde omnis iste natus error sit voluptatem accusantium doloremque laudantium, totam rem aperiam, eaque ipsa quae ab illo.</div>
      <div class="read-more" style="font-size:16px;margin-top:12px;text-decoration:underline">Read More</div>
    </div>
  </article>

  <article class="news-card" style="left:606px;top:2598px;width:484px;height:170px;display:flex">
    <div role="img" aria-label="Neon cloud above data grid" style="width:205px;background:radial-gradient(circle at 50% 45%,#4ab8e6 0%,#145c8c 45%,#0b1c33 100%)"></div>
    <div style="padding:16px 12px">
      <div class="news-title" style="font-size:16px;line-height:22px">Perspiciatis undeomnis iste natus errosit</div>
      <div class="news-body" style="font-size:11.5px;line-height:20px;margin-top:4px">Sedut perspiciatis unde omnis iste natus error sit voluptatem accusantium doloremque laudantium.</div>
      <div class="read-more" style="font-size:13px;margin-top:8px">Read More</div>
    </div>
  </article>
  <article class="news-card" style="left:606px;top:2796px;width:484px;height:168px;display:flex">
    <div role="img" aria-label="Cloud icon linked to a secure device" style="width:205px;background:linear-gradient(160deg,#1b6bd0,#0b2f6a 60%,#1a1030)"></div>
    <div style="padding:16px 12px">
      <div class="news-title" style="font-size:16px;line-height:22px">Perspiciatis undeomnis iste natus errosit</div>
      <div class="news-body" style="font-size:11.5px;line-height:20px;margin-top:4px">Sedut perspiciatis unde omnis iste natus error sit voluptatem accusantium doloremque laudantium.</div>
      <div class="read-more" style="font-size:13px;margin-top:8px">Read More</div>
    </div>
  </article>
  <article class="news-card" style="left:606px;top:2994px;width:484px;height:168px;display:flex">
    <div role="img" aria-label="Server racks lit in blue light" style="width:205px;background:linear-gradient(90deg,#0c3f8e,#3aa7e8 50%,#0c3f8e)"></div>
    <div style="padding:16px 12px">
      <div class="news-title" style="font-size:16px;line-height:22px">Perspiciatis undeomnis iste natus errosit</div>
      <div class="news-body" style="font-size:11.5px;line-height:20px;margin-top:4px">Sedut perspiciatis unde omnis iste natus error sit voluptatem accusantium doloremque laudantium.</div>
      <div class="read-more" style="font-size:13px;margin-top:8px">Read More</div>
    </div>
  </article>
  <div class="btn" style="left:515px;top:3206px;width:170px;height:40px;background:#fff;color:var(--navy);font-weight:600">View all</div>
</section>

<!-- contact -->
<section class="contact">
  <h2 class="heading abs" style="left:0;width:1200px;text-align:center;top:3432px">Contact <span class="accent">us</span></h2>
  <div class="rule" style="left:559px;top:3485px"></div>
  <p class="abs" style="left:0;width:1200px;text-align:center;top:3505px;font-size:13.5px;line-height:26px;color:#3a3a3a">Sed ut perspiciatis unde omnis iste natus error sit voluptatem accusantium doloremque laudantium<br>totam remaperiam eaque ipsaqueaelo</p>
  <div class="field" style="left:279px;top:3578px;width:313px;height:52px"><svg width="14" height="14" viewBox="0 0 14 14"><circle cx="7" cy="4" r="3.2" fill="#0a3d91"/><path d="M1 14c0-4 3-6 6-6s6 2 6 6z" fill="#0a3d91"/></svg>First name</div>
  <div class="field" style="left:607px;top:3578px;width:313px;height:52px"><svg width="14" height="14" viewBox="0 0 14 14"><circle cx="7" cy="4" r="3.2" fill="#0a3d91"/><path d="M1 14c0-4 3-6 6-6s6 2 6 6z" fill="#0a3d91"/></svg>Last name</div>
  <div class="field" style="left:279px;top:3654px;width:313px;height:53px"><svg width="16" height="12" viewBox="0 0 16 12"><rect x="0.5" y="0.5" width="15" height="11" fill="#0a3d91"/><path d="M1 1l7 6 7-6" fill="none" stroke="#fff" stroke-width="1.2"/></svg>Email</div>
  <div class="field" style="left:607px;top:3654px;width:313px;height:53px"><svg width="14" height="14" viewBox="0 0 14 14"><path d="M3 1l3 3-1.5 2c1 2 2 3 3.5 3.5L10 8l3 3-2 2C6 13 1 8 1 3z" fill="#0a3d91"/></svg>Phone</div>
  <div class="field" style="left:279px;top:3730px;width:641px;height:111px;align-items:flex-start;padding-top:20px"><svg width="14" height="14" viewBox="0 0 14 14"><path d="M1 1l12 12" stroke="#0a3d91" stroke-width="2.4"/></svg>Message</div>
  <div class="btn" style="left:513px;top:3856px;width:172px;height:42px">Submit</div>
</section>

<!-- footer -->
<footer class="footer">
  <svg class="abs" style="left:0;top:3980px" width="1200" height="60" viewBox="0 0 1200 60">
    <polygon points="0,50 420,14 860,0 1200,40 1200,60 0,60" fill="#1ba3e0"/>
    <polygon points="0,58 420,24 860,10 1200,50 1200,60 0,60" fill="#03060d"/>
  </svg>
  <div class="abs" role="img" aria-label="Dark particle wave backdrop" style="left:0;top:4038px;width:1200px;height:394px;background:radial-gradient(circle at 60% 100%,#1b2433 0%,#070b13 55%,#03060d 100%)"></div>
  <div class="abs" style="left:110px;top:4140px;display:flex;align-items:center;gap:12px">
    <span style="width:46px;height:46px;border-radius:50%;background:var(--deep)"></span>
    <span style="font-weight:700;font-size:30px;color:#fff;letter-spacing:1.5px">VORPLEXA</span>
  </div>
  <div class="abs" style="left:110px;top:4200px;font-size:11px;font-weight:600;color:#fff;letter-spacing:.3px">EFFECTIVE TECHNOLOGY MANAGEMENT</div>
  <div class="social" style="left:130px;top:4337px" aria-label="Social profile one"></div>
  <div class="social" style="left:192px;top:4337px" aria-label="Social profile two"></div>
  <div class="social" style="left:253px;top:4337px" aria-label="Social profile three"></div>

  <div class="foot-head" style="left:415px;top:4142px">Quick links</div>
  <ul class="foot-list" style="left:415px;top:4186px"><li>Home</li><li>What we do</li><li>Resources</li><li>Company</li><li>Contact</li></ul>
  <div class="foot-head" style="left:615px;top:4142px">Links</div>
  <ul class="foot-list" style="left:615px;top:4186px"><li>FAQ'S</li><li>Terms &amp; conditions</li><li>Privacy policy</li><li>Site map</li></ul>
  <div class="foot-head" style="left:855px;top:4142px">Contact us</div>
  <svg class="abs" style="left:852px;top:4192px" width="18" height="24" viewBox="0 0 18 24"><path d="M9 1a7 7 0 0 1 7 7c0 6-7 15-7 15S2 14 2 8a7 7 0 0 1 7-7z" fill="#33a6d7"/><circle cx="9" cy="8" r="2.6" fill="#03060d"/></svg>
  <div class="abs" style="left:886px;top:4190px;font-size:13px;line-height:26px;color:#e6ecf5">218 Brindle Court, Halverton,<br>Ohio, 44510, USA</div>
  <svg class="abs" style="left:852px;top:4264px" width="18" height="18" viewBox="0 0 14 14"><path d="M3 1l3 3-1.5 2c1 2 2 3 3.5 3.5L10 8l3 3-2 2C6 13 1 8 1 3z" fill="#33a6d7"/></svg>
  <div class="abs" style="left:886px;top:4264px;font-size:13px;color:#e6ecf5">555-014-2290</div>
  <svg class="abs" style="left:852px;top:4311px" width="20" height="14" viewBox="0 0 16 12"><rect x="0.5" y="0.5" width="15" height="11" fill="#33a6d7"/><path d="M1 1l7 6 7-6" fill="none" stroke="#03060d" stroke-width="1.2"/></svg>
  <div class="abs" style="left:886px;top:4308px;font-size:13px;color:#e6ecf5">hello@vorplexa-mail.test</div>

  <div class="bottom-bar abs">
    <div class="abs" style="left:110px;top:30px">Copyright © 2021.&nbsp; All rights reserved</div>
    <div class="abs" style="left:802px;top:30px">Privacy Notice</div>
    <div class="abs" style="left:937px;top:6px;width:1px;height:38px;background:#fff"></div>
    <div class="abs" style="left:965px;top:30px">Conditions of Use</div>
  </div>
  <svg class="abs" style="left:1114px;top:4412px" width="40" height="40" viewBox="0 0 40 40"><circle cx="20" cy="20" r="18" fill="#fff"/><path d="M14 23l6-6 6 6" fill="none" stroke="#06357f" stroke-width="2" stroke-linecap="round"/></svg>
</footer>

</body>
</html>
```